Lendquay wedsite and logo refresh

We are looking for someone to refresh the look and feel of Lendquay.co.nz we are moving it towards a more traditional brokerage.

Target Market(s)

30 to 55 year old professionals

Coding

Coded - Design and coding required

Number of Pages Required

3 page

Requirements
Nice to have
• we are needing a modern professional look

```html
<!DOCTYPE html>
<html lang="en">
<head>
<meta charset="utf-8">
<title>Lendquay – Find and Compare Rates</title>
<link href="https://fonts.googleapis.com/css2?family=Roboto:wght@400;500;700;900&display=swap" rel="stylesheet">
<style>
:root{
  --red:#e8452c;
  --red-dark:#c9361f;
  --ink:#222222;
  --muted:#666666;
  --line:#dddddd;
  --panel:#f1f1f1;
  --white:#ffffff;
  --footer:#1d1d1d;
  --footer-bar:#141414;
}
*{margin:0;padding:0;box-sizing:border-box}
html,body{width:1200px;height:2908px;overflow:hidden}
body{position:relative;background:var(--white);font-family:"Roboto",Arial,sans-serif;color:var(--ink)}
.abs{position:absolute}

/* header */
.site-header{left:0;top:0;width:1200px;height:80px;background:var(--white);display:flex;align-items:center}
.brand{position:absolute;left:112px;top:18px;font-weight:900;font-size:40px;letter-spacing:1px;color:var(--red);line-height:44px}
.main-nav{position:absolute;left:380px;top:30px;display:flex;gap:34px;font-size:15px;font-weight:700;letter-spacing:.5px}
.btn-login{position:absolute;left:728px;top:22px;width:80px;height:36px;border:2px solid var(--red);color:var(--red);font-size:14px;font-weight:700;display:flex;align-items:center;justify-content:center}
.btn-signup{position:absolute;left:820px;top:22px;width:164px;height:36px;background:var(--red);color:var(--white);font-size:14px;font-weight:700;display:flex;align-items:center;justify-content:center}
.lang{position:absolute;left:998px;top:32px;display:flex;align-items:center;gap:6px;font-size:12px;font-weight:500;color:var(--muted)}
.lang-flag{width:22px;height:14px;background:#2a3f7a}

/* hero */
.hero{left:0;top:80px;width:1200px;height:592px;background:linear-gradient(180deg,#dfe3e6 0%,#c9cfc9 38%,#8d9a7a 70%,#5f7a3c 100%)}
.hero-copy{position:absolute;left:660px;top:150px;color:var(--white);font-weight:900;font-size:64px;line-height:62px;letter-spacing:1px}
.hero-cta{position:absolute;left:660px;top:360px;width:296px;height:52px;background:var(--red);color:var(--white);font-weight:700;font-size:16px;letter-spacing:.5px;display:flex;align-items:center;justify-content:center}
.hero-dots{position:absolute;left:548px;top:546px;display:flex;gap:10px}
.hero-dots span{width:12px;height:12px;border-radius:50%;background:rgba(255,255,255,.6)}
.hero-dots span.active{background:var(--white)}

/* rates grid */
.section-title{font-weight:900;font-size:28px;letter-spacing:1px;text-align:center;width:1200px;left:0}
.rates-title{top:712px}
.rate-card{width:216px;height:160px;border:1px solid var(--line);background:var(--white);display:flex;flex-direction:column;align-items:center}
.rate-card svg{margin-top:38px;width:56px;height:56px;fill:none;stroke:var(--ink);stroke-width:3;stroke-linejoin:round;stroke-linecap:round}
.rate-card .label{margin-top:16px;font-size:12px;font-weight:700;letter-spacing:.3px;text-align:center;line-height:15px}
.rate-card.featured{background:var(--red);border-color:var(--red);color:var(--white)}
.rate-card.featured svg{stroke:var(--white)}

/* why */
.why{left:0;top:1376px;width:1200px;height:692px;background:var(--panel)}
.why-title{top:1420px}
.why-item{width:290px;display:flex;gap:20px}
.why-icon{flex:0 0 48px;width:48px;height:48px;background:var(--red);display:flex;align-items:center;justify-content:center}
.why-icon svg{width:28px;height:28px;fill:none;stroke:var(--white);stroke-width:2.6;stroke-linecap:round;stroke-linejoin:round}
.why-item h3{font-size:14px;font-weight:900;letter-spacing:.3px;margin-bottom:8px}
.why-item p{font-size:12px;line-height:17px;color:var(--muted)}
.why-photo{left:440px;top:1512px;width:312px;height:320px;background:linear-gradient(135deg,#e6e8ea 0%,#c7ccd2 55%,#9aa2ab 100%)}
.btn-start{left:512px;top:1868px;width:176px;height:52px;background:var(--red);color:var(--white);font-size:16px;font-weight:700;display:flex;align-items:center;justify-content:center}

/* team */
.team-title{top:2012px}
.member{width:300px;display:flex;flex-direction:column;align-items:center}
.member-photo{width:300px;height:212px;background:linear-gradient(180deg,#eeeeee 0%,#cfcfcf 60%,#2a2a2a 100%)}
.member-name{margin-top:22px;font-size:15px;font-weight:900;letter-spacing:.3px}
.member-role{margin-top:4px;font-size:13px;font-weight:700;color:var(--muted)}
.btn-more{margin-top:12px;width:76px;height:22px;border:1px solid var(--red);color:var(--red);font-size:10px;font-weight:700;display:flex;align-items:center;justify-content:center}

/* footer */
.site-footer{left:0;top:2452px;width:1200px;height:388px;background:var(--footer);color:#cfcfcf}
.footer-brand{position:absolute;left:180px;top:208px;font-weight:900;font-size:40px;letter-spacing:1px;color:var(--red)}
.footer-col{position:absolute;top:72px}
.footer-col h4{color:var(--white);font-size:14px;font-weight:900;letter-spacing:.5px;margin-bottom:18px}
.footer-col li{list-style:none;font-size:12px;line-height:22px}
.contact-row{display:flex;align-items:center;gap:14px;margin-bottom:20px;font-size:12px;line-height:16px}
.dot-icon{flex:0 0 36px;width:36px;height:36px;border-radius:50%;background:var(--red);display:flex;align-items:center;justify-content:center}
.dot-icon svg{width:18px;height:18px;fill:none;stroke:var(--white);stroke-width:2.2;stroke-linecap:round;stroke-linejoin:round}
.footer-bar{left:0;top:2840px;width:1200px;height:68px;background:var(--footer-bar);color:#8a8a8a;font-size:11px;display:flex;align-items:center;justify-content:center}
</style>
</head>
<body>

<header class="site-header abs">
  <div class="brand">LENDQUAY</div>
  <nav class="main-nav"><span>HOME</span><span>ABOUT</span><span>SERVICES</span><span>CONTACT</span></nav>
  <div class="btn-login">LOGIN</div>
  <div class="btn-signup">SIGN UP FOR FREE</div>
  <div class="lang"><span class="lang-flag"></span>EN</div>
</header>

<section class="hero abs" role="img" aria-label="Happy family jumping on the lawn in front of their new house">
  <div class="hero-copy">NO OBLIGATIONS<br>NO FEES<br>NO WORRIES</div>
  <div class="hero-cta">FIND AND COMPARE RATES</div>
  <div class="hero-dots"><span></span><span class="active"></span><span></span><span></span><span></span></div>
</section>

<h2 class="section-title rates-title abs">FIND COMPARE RATES</h2>

<div class="rate-card abs" style="left:160px;top:808px"><svg viewBox="0 0 56 56"><path d="M6 28 28 10l22 18"/><path d="M12 24v22h32V24"/><path d="M24 46V34h8v12"/></svg><div class="label">MORTGAGE RATES</div></div>
<div class="rate-card abs" style="left:384px;top:808px"><svg viewBox="0 0 56 56"><ellipse cx="28" cy="32" rx="18" ry="13"/><path d="M18 44v6M38 44v6M46 30h4"/><circle cx="22" cy="28" r="1.5"/><path d="M24 18h8"/></svg><div class="label">PERSONAL FINANCE</div></div>
<div class="rate-card abs" style="left:608px;top:808px"><svg viewBox="0 0 56 56"><path d="M6 30 28 14l22 16"/><path d="M14 46V36h28v10"/><circle cx="20" cy="46" r="3"/><circle cx="36" cy="46" r="3"/></svg><div class="label">VEHICLE FINANCE</div></div>
<div class="rate-card abs" style="left:832px;top:808px"><svg viewBox="0 0 56 56"><rect x="8" y="18" width="40" height="28" rx="2"/><path d="M21 18v-6h14v6M8 30h40"/></svg><div class="label">BUSINESS &amp; ASSET FINANCE</div></div>

<div class="rate-card abs" style="left:160px;top:988px"><svg viewBox="0 0 56 56"><rect x="10" y="10" width="22" height="38"/><path d="M32 22h14v26H32M16 18h4M22 18h4M16 26h4M22 26h4M16 34h4M22 34h4M6 48h44"/></svg><div class="label">COMMERCIAL FINANCE</div></div>
<div class="rate-card featured abs" style="left:384px;top:988px"><svg viewBox="0 0 56 56"><rect x="12" y="8" width="32" height="40" rx="2"/><path d="M18 18h20M18 26h20M18 34h12"/><circle cx="38" cy="42" r="7"/></svg><div class="label">INSURANCE RATES</div></div>
<div class="rate-card abs" style="left:608px;top:988px"><svg viewBox="0 0 56 56"><rect x="8" y="22" width="30" height="16" rx="4"/><circle cx="16" cy="40" r="4"/><circle cx="32" cy="40" r="4"/><circle cx="42" cy="16" r="6"/><path d="M42 22v14"/></svg><div class="label">VEHICLE LEASING</div></div>
<div class="rate-card abs" style="left:832px;top:988px"><svg viewBox="0 0 56 56"><path d="M8 28a20 20 0 0 1 40 0z"/><path d="M28 28v16a4 4 0 0 1-8 0"/></svg><div class="label">HOME, CONTENTS &amp;<br>CAR INSURANCE</div></div>

<div class="rate-card abs" style="left:160px;top:1168px"><svg viewBox="0 0 56 56"><path d="M20 36a14 14 0 1 1 16 0v6H20z"/><path d="M22 48h12M28 4v2M8 22h2M46 22h2"/></svg><div class="label">POWER &amp; GAS</div></div>
<div class="rate-card abs" style="left:384px;top:1168px"><svg viewBox="0 0 56 56"><path d="M6 22a32 32 0 0 1 44 0M13 30a22 22 0 0 1 30 0M20 38a12 12 0 0 1 16 0"/><circle cx="28" cy="45" r="2"/></svg><div class="label">INTERNET &amp; FIBRE</div></div>
<div class="rate-card abs" style="left:608px;top:1168px"><svg viewBox="0 0 56 56"><rect x="10" y="20" width="36" height="26" rx="3"/><path d="M14 20c0-8 28-8 28 0M22 28h12v10H22z"/></svg><div class="label">PHONE &amp; MOBILE</div></div>
<div class="rate-card abs" style="left:832px;top:1168px"><svg viewBox="0 0 56 56"><path d="M8 24 28 10l20 14v24H8z"/><path d="M20 48V32h16v16M20 32l16 16M36 32 20 48"/></svg><div class="label">FARMING &amp;<br>RURAL INSURANCE</div></div>

<section class="why abs"></section>
<h2 class="section-title why-title abs">WHY LENDQUAY?</h2>

<div class="why-item abs" style="left:128px;top:1540px">
  <div class="why-icon"><svg viewBox="0 0 28 28"><path d="M6 20l6-6 4 4 7-8"/><path d="M18 10h5v5"/></svg></div>
  <div><h3>GREAT RATES &amp; INCENTIVES</h3><p>Receive the great rates and incentives banks offer brokers, with no need to shop around yourself.</p></div>
</div>
<div class="why-item abs" style="left:128px;top:1700px">
  <div class="why-icon"><svg viewBox="0 0 28 28"><circle cx="14" cy="14" r="10"/><path d="M14 8v6l4 3"/></svg></div>
  <div><h3>ANY TIME, ANY WHERE</h3><p>Get notifications and review representative offers wherever you are with your personal, mobile-friendly dashboard.</p></div>
</div>
<div class="why-photo abs" role="img" aria-label="Hands reviewing finance documents at a desk"></div>
<div class="why-item abs" style="left:784px;top:1540px">
  <div class="why-icon"><svg viewBox="0 0 28 28"><path d="M14 4 5 8v6c0 6 4 9 9 11 5-2 9-5 9-11V8z"/><path d="M10 14l3 3 5-6"/></svg></div>
  <div><h3>PRIVACY IS IMPORTANT</h3><p>Your private information is disclosed only when you choose a representative offer from a service provider.</p></div>
</div>
<div class="why-item abs" style="left:784px;top:1700px">
  <div class="why-icon"><svg viewBox="0 0 28 28"><circle cx="14" cy="14" r="10"/><path d="M7 21 21 7"/></svg></div>
  <div><h3>NO FEES, NO OBLIGATIONS</h3><p>The service is free and you are under no obligation until you select the representative offer that suits you best.</p></div>
</div>
<div class="btn-start abs">GET STARTED</div>

<h2 class="section-title team-title abs">MEET THE TEAM</h2>
<div class="member abs" style="left:128px;top:2088px">
  <div class="member-photo" role="img" aria-label="Portrait of Daniel Hart in a dark branded t-shirt"></div>
  <div class="member-name">DANIEL HART</div><div class="member-role">CEO</div><div class="btn-more">READ MORE</div>
</div>
<div class="member abs" style="left:450px;top:2088px">
  <div class="member-photo" role="img" aria-label="Portrait of Owen Price in a dark branded t-shirt"></div>
  <div class="member-name">OWEN PRICE</div><div class="member-role">FOUNDER</div><div class="btn-more">READ MORE</div>
</div>
<div class="member abs" style="left:772px;top:2088px">
  <div class="member-photo" role="img" aria-label="Portrait of Ravi Sandhu in a dark branded t-shirt"></div>
  <div class="member-name">RAVI SANDHU</div><div class="member-role">CHIEF OPERATIONS OFFICER</div><div class="btn-more">READ MORE</div>
</div>

<footer class="site-footer abs">
  <div class="footer-brand">LENDQUAY</div>
  <div class="footer-col" style="left:500px">
    <h4>MENU</h4>
    <ul><li>HOME</li><li>ABOUT</li><li>SERVICES</li><li>CONTACT</li></ul>
  </div>
  <div class="footer-col" style="left:688px">
    <h4>CONTACT US</h4>
    <div class="contact-row"><span class="dot-icon"><svg viewBox="0 0 18 18"><path d="M9 16s5-5 5-9a5 5 0 0 0-10 0c0 4 5 9 5 9z"/><circle cx="9" cy="7" r="1.6"/></svg></span><span>12 Harbour View Road,<br>Auckland 1010</span></div>
    <div class="contact-row"><span class="dot-icon"><svg viewBox="0 0 18 18"><path d="M4 2h3l1.5 4-2 1.5a9 9 0 0 0 4 4l1.5-2 4 1.5v3a2 2 0 0 1-2 2A14 14 0 0 1 2 4a2 2 0 0 1 2-2z"/></svg></span><span>09 555 0142</span></div>
    <div class="contact-row"><span class="dot-icon"><svg viewBox="0 0 18 18"><rect x="2" y="4" width="14" height="10" rx="1"/><path d="m2 5 7 5 7-5"/></svg></span><span>info@lendquay.co.nz</span></div>
  </div>
  <div class="footer-col" style="left:952px">
    <h4>FOLLOW US</h4>
    <div class="contact-row"><span class="dot-icon"></span><span>Like our page</span></div>
    <div class="contact-row"><span class="dot-icon"></span><span>Follow our feed</span></div>
    <div class="contact-row"><span class="dot-icon"></span><span>Connect with us</span></div>
  </div>
</footer>
<div class="footer-bar abs">Copyright © 2024 All Rights Reserved</div>

</body>
</html>
```